A website for a Maltese Law Firm

Our law firm needs a website to further its business. The site should have a simple yet effective design. We would need the following sections: About us, Practice Areas, About Malta, Contact. These should be further split as follows:

About us: Our firm, Our values, What others say, Offices

Practice Areas: Crimimal, Citizenship & Residence, Sovereign Patron Pathway, Criminal Defence, Civil Litigation, Arbitration and ADR, Commercial and Corporate, Media Law.

About Malta: just one section.

Contact: Just one section

We would also need a news feed at the front of the site to include latest news regarding our cases.

At the bottom we need a section for our Terms and a Privacy Statement.

Our logo is being attached.

Target Market(s)

All clients looking for legal assistance in Malta

Industry/Entity Type

Legal

Coding

Coded - Design and coding required

Number of Pages Required

1 page

Requirements
Must have
• It must be simple yet striking.

```html
<!DOCTYPE html>
<html lang="en">
<head>
<meta charset="utf-8">
<title>Mallia &amp; Sant Advocates</title>
<link rel="stylesheet" href="https://fonts.googleapis.com/css2?family=Cinzel:wght@400;600&family=Open+Sans:wght@400;600;700&display=swap">
<style>
:root{
  --ink:#111;
  --black:#000;
  --white:#fff;
  --grey-bg:#f1f1f1;
  --grey-mid:#9a9a9a;
  --grey-dark:#555;
  --text:#333;
  --footer:#141414;
  --btn:#2b2b2b;
  --line:#222;
}
*{box-sizing:border-box;margin:0;padding:0}
html,body{width:1200px;height:2731px;overflow:hidden;background:var(--white)}
body{font-family:"Open Sans",Arial,sans-serif;color:var(--text);position:relative}

/* header */
.site-header{position:absolute;top:0;left:0;width:1200px;height:140px}
.brand{position:absolute;left:32px;top:48px;font-family:"Cinzel",Georgia,serif;font-size:32px;font-weight:400;color:var(--ink);letter-spacing:.5px;white-space:nowrap}
.header-contact{position:absolute;top:56px;display:flex;align-items:center;gap:10px;font-size:14px;font-weight:600;color:#555;line-height:1.25;white-space:nowrap}
.header-contact.phone{left:672px}
.header-contact.mail{left:950px}
.icon-ring{width:32px;height:32px;border:2px solid #777;border-radius:50%;display:flex;align-items:center;justify-content:center;flex:none}

/* nav */
.main-nav{position:absolute;top:140px;left:0;width:1200px;height:42px;background:var(--black)}
.main-nav a{position:absolute;top:0;height:42px;line-height:42px;color:var(--white);text-decoration:none;font-family:"Cinzel",Georgia,serif;font-size:16px;white-space:nowrap}
.main-nav a.active{background:#4a4a4a;width:130px;text-align:center}

/* hero */
.hero{position:absolute;top:182px;left:0;width:1200px;height:503px}
.hero-photo{position:absolute;inset:0;background:radial-gradient(ellipse at 30% 40%,#e7b770 0%,#a76a2a 35%,#6b3c14 70%,#3e210b 100%)}
.hero-copy{position:absolute;left:541px;top:148px;width:620px;color:var(--white)}
.hero-copy h1{font-family:"Cinzel",Georgia,serif;font-weight:400;font-size:26px;margin-bottom:10px;white-space:nowrap}
.hero-copy p{font-size:15.5px;line-height:1.32}
.btn-dark{display:inline-block;background:var(--btn);color:var(--white);font-weight:700;text-align:center;border-radius:4px}
.hero-copy .btn-dark{margin-top:34px;width:235px;height:48px;line-height:48px;font-size:22px}

/* section headings */
.section-title{position:absolute;left:0;width:100%;text-align:center}
.section-title span{display:inline-block;font-family:"Cinzel",Georgia,serif;font-size:28px;color:var(--ink);border-top:2px solid currentColor;border-bottom:2px solid currentColor;padding:4px 6px 2px;line-height:1.3}

/* practice areas */
.practice{position:absolute;top:685px;left:0;width:1200px;height:775px;background:var(--white)}
.practice .section-title{top:50px}
.connectors{position:absolute;inset:0}
.area-card{position:absolute;width:228px;height:149px;border:4px solid #eee;box-shadow:0 0 3px rgba(0,0,0,.15)}
.area-card .photo{position:absolute;inset:0}
.area-card .label{position:absolute;left:0;right:0;height:28px;line-height:28px;background:rgba(30,30,30,.85);color:var(--white);text-align:center;font-family:"Cinzel",Georgia,serif;font-size:17px;white-space:nowrap}
.top-row .label{top:0}
.bottom-row .label{bottom:0}
.area-icon{position:absolute;width:60px;height:60px;border-radius:50%;background:#3b3b3b;border:5px solid var(--white);box-shadow:0 0 3px rgba(0,0,0,.3);display:flex;align-items:center;justify-content:center}
.firm-box{position:absolute;left:418px;top:396px;width:363px;height:88px;border:3px solid var(--line);border-radius:8px;background:var(--white);display:flex;align-items:center;justify-content:center;text-align:center;white-space:nowrap;font-family:"Cinzel",Georgia,serif;font-size:21px;color:var(--ink)}

/* about malta */
.about-malta{position:absolute;top:1460px;left:0;width:1200px;height:500px}
.about-malta .backdrop{position:absolute;inset:0;background:linear-gradient(180deg,#18243a 0%,#33435c 40%,#6b6a5e 65%,#2a3a40 100%)}
.about-malta .section-title span{color:var(--white)}
.about-malta .section-title{top:52px}
.malta-photo{position:absolute;left:69px;top:130px;width:510px;height:320px;border:5px solid var(--white);background:linear-gradient(180deg,#5a8fc8 0%,#c8b48a 45%,#4f8f8a 70%,#2f6f6a 100%)}
.malta-copy{position:absolute;left:659px;top:130px;width:520px;color:var(--white);font-size:16px;line-height:1.3}
.btn-light{display:inline-block;background:var(--white);color:var(--ink);font-weight:700;font-size:17px;width:182px;height:38px;line-height:38px;text-align:center;border-radius:3px;margin-top:30px}

/* news & message */
.news-contact{position:absolute;top:1960px;left:0;width:1200px;height:388px;background:var(--grey-bg)}
.col-title{position:absolute;top:52px}
.col-title span{display:inline-block;font-family:"Cinzel",Georgia,serif;font-size:28px;color:var(--ink);border-top:2px solid currentColor;border-bottom:2px solid currentColor;padding:3px 6px 1px;white-space:nowrap}
.news-item{position:absolute;left:77px;width:470px;display:flex;gap:20px}
.news-date{width:82px;flex:none;text-align:center;background:var(--white)}
.news-date .dm{background:var(--grey-mid);color:var(--white);padding:4px 0 3px}
.news-date .day{font-size:30px;font-weight:700;line-height:1}
.news-date .mon{font-size:14px;font-weight:700;line-height:1.1}
.news-date .year{font-size:17px;font-weight:700;color:var(--ink);padding:5px 0}
.news-body h3{font-size:15px;font-weight:700;color:var(--ink);margin-bottom:2px}
.news-body p{font-size:15px;line-height:1.3;color:#444}
.message-form{position:absolute;left:740px;top:130px;width:308px}
.field{background:var(--white);height:32px;font-size:11px;padding:6px 8px;color:#333;margin-bottom:6px}
.field.tall{height:70px}
.submit{display:inline-block;background:var(--btn);color:var(--white);font-weight:700;font-size:13px;width:108px;height:28px;line-height:28px;text-align:center;border-radius:2px;margin-top:2px}

/* footer */
.site-footer{position:absolute;top:2348px;left:0;width:1200px;height:328px;background:var(--white)}
.footer-shape{position:absolute;inset:0}
.footer-col{position:absolute;top:42px;color:var(--white)}
.footer-col h4{font-size:16px;font-weight:700;margin-bottom:14px}
.footer-col li{list-style:none;font-size:13px;font-weight:600;line-height:21px;text-transform:uppercase;white-space:nowrap}
.office-line{display:flex;align-items:center;gap:10px;font-size:14px;font-weight:600;margin-bottom:10px;white-space:nowrap}
.footer-brand{position:absolute;left:866px;top:127px;width:310px;text-align:center;white-space:nowrap;font-family:"Cinzel",Georgia,serif;font-size:19px;color:var(--ink);border-top:1px solid #444;border-bottom:1px solid #444;padding:4px 0 3px}
.social{position:absolute;left:984px;top:182px;display:flex;gap:10px}
.social span{width:18px;height:18px;border-radius:50%;background:#888}
.copyright{position:absolute;top:2676px;left:0;width:1200px;height:55px;background:#5b5b5b;color:#ddd;font-size:11px;font-weight:700;text-align:center;line-height:55px;letter-spacing:.2px}
</style>
</head>
<body>

<header class="site-header">
  <div class="brand">Mallia &amp; Sant Advocates</div>
  <div class="header-contact phone">
    <span class="icon-ring"><svg width="16" height="16" viewBox="0 0 24 24"><path d="M6.6 10.8a15 15 0 0 0 6.6 6.6l2.2-2.2c.3-.3.7-.4 1-.2 1.1.4 2.3.6 3.6.6.6 0 1 .4 1 1V20c0 .6-.4 1-1 1A17 17 0 0 1 3 4c0-.6.4-1 1-1h3.5c.6 0 1 .4 1 1 0 1.3.2 2.5.6 3.6.1.3 0 .7-.2 1z" fill="#777"/></svg></span>
    <span>(356) 2100 0001 - Valletta<br>(356) 2100 0002 - Birkirkara</span>
  </div>
  <div class="header-contact mail">
    <span class="icon-ring"><svg width="16" height="12" viewBox="0 0 16 12"><rect x="1" y="1" width="14" height="10" fill="none" stroke="#777" stroke-width="1.6"/><path d="M1 1l7 6 7-6" fill="none" stroke="#777" stroke-width="1.6"/></svg></span>
    <span>info@mallia-sant.example</span>
  </div>
</header>

<nav class="main-nav">
  <a class="active" style="left:170px">Home</a>
  <a style="left:337px">About Us ▾</a>
  <a style="left:502px">Practice Areas ▾</a>
  <a style="left:718px">About Malta</a>
  <a style="left:903px">Contact</a>
</nav>

<section class="hero">
  <div class="hero-photo" role="img" aria-label="Brass scales of justice on a desk in a warmly lit courtroom"></div>
  <div class="hero-copy">
    <h1>Welcome to Mallia &amp; Sant Advocates</h1>
    <p>Lorem ipsum dolor sit amet, consectetuer adipiscing elit, sed diam nonummy nibh euismod tincidunt ut laoreet dolore magna aliquamerat volutpat. Ut wisi enim ad minim veniam, quis nostrud exerci tation ullamcorper suscipit lobortis nisl ut aliq uip ex ea commodo consequat. Duis autem vel eum iriure dolor in hendrerit in vulputate velit esse molestie consequat, vel illum dolore eu feugiat nulla.</p>
    <span class="btn-dark">Contact Us</span>
  </div>
</section>

<section class="practice">
  <div class="section-title"><span>Practice Areas</span></div>

  <svg class="connectors" width="1200" height="775" viewBox="0 0 1200 775">
    <g stroke="#333" stroke-width="2" stroke-dasharray="2 5" fill="none">
      <line x1="216" y1="316" x2="420" y2="400"/>
      <line x1="474" y1="316" x2="540" y2="398"/>
      <line x1="730" y1="316" x2="664" y2="398"/>
      <line x1="982" y1="316" x2="780" y2="400"/>
      <line x1="216" y1="572" x2="420" y2="480"/>
      <line x1="474" y1="572" x2="540" y2="482"/>
      <line x1="730" y1="572" x2="664" y2="482"/>
      <line x1="982" y1="572" x2="780" y2="480"/>
    </g>
  </svg>

  <div class="top-row">
    <div class="area-card" style="left:101px;top:157px"><div class="photo" role="img" aria-label="Burning car at night" style="background:linear-gradient(160deg,#3a2a22,#d8641c 55%,#f2a23a)"></div><div class="label">Criminal</div></div>
    <div class="area-card" style="left:356px;top:157px"><div class="photo" role="img" aria-label="Hand holding a passport" style="background:linear-gradient(160deg,#5b6f8e,#c9ccd4 50%,#2d3c5a)"></div><div class="label">Citizenship</div></div>
    <div class="area-card" style="left:612px;top:157px"><div class="photo" role="img" aria-label="Business meeting at a table" style="background:linear-gradient(160deg,#dfe6ee,#7b8fa6 55%,#3c4a5e)"></div><div class="label">Sovereign Patron</div></div>
    <div class="area-card" style="left:870px;top:157px"><div class="photo" role="img" aria-label="Handcuffed hands in a suit" style="background:linear-gradient(160deg,#2b2b30,#b05060 55%,#1e1e22)"></div><div class="label">Criminal Defence</div></div>
  </div>

  <div class="bottom-row">
    <div class="area-card" style="left:101px;top:582px"><div class="photo" role="img" aria-label="Scales of justice" style="background:linear-gradient(160deg,#7a4a1c,#e2a45a 50%,#5a3210)"></div><div class="label">Civil Litigation</div></div>
    <div class="area-card" style="left:356px;top:582px"><div class="photo" role="img" aria-label="Gavel on an arbitration hearing document" style="background:linear-gradient(160deg,#e6e2da,#b8ad9c 55%,#5a4634)"></div><div class="label">Arbitration &amp; ADR</div></div>
    <div class="area-card" style="left:612px;top:582px"><div class="photo" role="img" aria-label="Business team in an office" style="background:linear-gradient(160deg,#e8edf2,#8aa0b8 55%,#34455c)"></div><div class="label">Commercial</div></div>
    <div class="area-card" style="left:870px;top:582px"><div class="photo" role="img" aria-label="Hand signing a document with a pen" style="background:linear-gradient(160deg,#7a5238,#c8b6a4 50%,#3a2a20)"></div><div class="label">Media Law</div></div>
  </div>

  <div class="area-icon" style="left:186px;top:286px"><svg width="26" height="26" viewBox="0 0 26 26" fill="none" stroke="#fff" stroke-width="2"><path d="M13 3v20M6 23h14M4 8h18M4 8l-3 7h6zM22 8l-3 7h6z"/></svg></div>
  <div class="area-icon" style="left:444px;top:286px"><svg width="24" height="26" viewBox="0 0 24 26" fill="none" stroke="#fff" stroke-width="2"><rect x="4" y="2" width="16" height="22" rx="1"/><circle cx="12" cy="10" r="4"/><path d="M8 18h8"/></svg></div>
  <div class="area-icon" style="left:700px;top:286px"><svg width="24" height="26" viewBox="0 0 24 26" fill="#fff"><circle cx="12" cy="7" r="5"/><path d="M2 25c0-6 4-10 10-10s10 4 10 10z"/></svg></div>
  <div class="area-icon" style="left:952px;top:286px"><svg width="26" height="26" viewBox="0 0 26 26" fill="none" stroke="#fff" stroke-width="2.4"><circle cx="8" cy="18" r="5"/><circle cx="18" cy="8" r="5"/><path d="M11 15l4-4"/></svg></div>

  <div class="area-icon" style="left:186px;top:552px"><svg width="26" height="26" viewBox="0 0 26 26" fill="none" stroke="#fff" stroke-width="2"><path d="M13 3v20M6 23h14M4 8h18M4 8l-3 7h6zM22 8l-3 7h6z"/></svg></div>
  <div class="area-icon" style="left:444px;top:552px"><svg width="26" height="26" viewBox="0 0 26 26" fill="#fff"><rect x="3" y="6" width="12" height="6" transform="rotate(-40 9 9)"/><rect x="9" y="11" width="3" height="12" transform="rotate(-40 10 17)"/><rect x="3" y="22" width="14" height="3"/></svg></div>
  <div class="area-icon" style="left:700px;top:552px"><svg width="24" height="26" viewBox="0 0 24 26" fill="none" stroke="#fff" stroke-width="2"><rect x="5" y="3" width="14" height="21"/><path d="M9 8h2M13 8h2M9 12h2M13 12h2M9 16h2M13 16h2"/></svg></div>
  <div class="area-icon" style="left:952px;top:552px"><svg width="26" height="24" viewBox="0 0 26 24" fill="none" stroke="#fff" stroke-width="2"><rect x="3" y="3" width="20" height="18"/><path d="M7 8h6v5H7zM16 8h3M16 12h3M7 16h12"/></svg></div>

  <div class="firm-box">Mallia &amp; Sant Advocates</div>
</section>

<section class="about-malta">
  <div class="backdrop" role="img" aria-label="Maltese harbour with colourful fishing boats under a dusk sky"></div>
  <div class="section-title"><span>About Malta</span></div>
  <div class="malta-photo" role="img" aria-label="Fishing boats moored in a Maltese harbour with town houses behind"></div>
  <div class="malta-copy">
    <p>Nam liber tempor cum soluta nobis eleifend option congue nihil imperdiet doming id quod mazim placerat facer possim assum. Typi non habent claritatem insitam; est usus legentis in iis qui facit eorum claritatem. Investigationes demonstrav erunt lectores legere me lius quod ii legunt saepius. Claritas est etiam processus dynamicus, qui sequitur mutationem consuetudium lectorum.</p>
    <span class="btn-light">More about Malta</span>
  </div>
</section>

<section class="news-contact">
  <div class="col-title" style="left:208px"><span>Latest News</span></div>
  <div class="col-title" style="left:745px"><span>Send Us a Message</span></div>

  <article class="news-item" style="top:132px">
    <div class="news-date"><div class="dm"><div class="day">01</div><div class="mon">SEP</div></div><div class="year">2015</div></div>
    <div class="news-body"><h3>Nam liber tempor cum soluta nobis</h3><p>Lorem ipsum dolor sit amet, consectetuer adipiscing elit, sed diam nonum my nibh euismod tincidunt ut laoreet dolore magna aliquam erat.</p></div>
  </article>
  <article class="news-item" style="top:240px">
    <div class="news-date"><div class="dm"><div class="day">24</div><div class="mon">AUG</div></div><div class="year">2015</div></div>
    <div class="news-body"><h3>Nam liber tempor cum soluta nobis</h3><p>Lorem ipsum dolor sit amet, consectetuer adipiscing elit, sed diam nonum my nibh euismod tincidunt ut laoreet dolore magna aliquam erat.</p></div>
  </article>

  <form class="message-form">
    <div class="field">Name</div>
    <div class="field">Email</div>
    <div class="field tall">Message</div>
    <span class="submit">SUBMIT</span>
  </form>
</section>

<footer class="site-footer">
  <svg class="footer-shape" width="1200" height="328" viewBox="0 0 1200 328"><polygon points="0,0 902,0 768,328 0,328" fill="#141414"/></svg>

  <div class="footer-col" style="left:53px">
    <h4>QUICK LINKS</h4>
    <ul><li>Home</li><li>About Us</li><li>Practice Areas</li><li>About Malta</li><li>Contact</li></ul>
  </div>
  <div class="footer-col" style="left:246px">
    <h4>PRACTICE AREAS</h4>
    <ul><li>Criminal</li><li>Citizenship &amp; Residence</li><li>Sovereign Patron Pathway</li><li>Criminal Defence</li><li>Civil Litigation</li><li>Arbitration &amp; ADR</li><li>Commercial &amp; Corporate</li><li>Media Law</li></ul>
  </div>
  <div class="footer-col" style="left:578px">
    <h4>VALETTA</h4>
    <div class="office-line"><svg width="18" height="18" viewBox="0 0 18 18"><circle cx="9" cy="9" r="8" fill="none" stroke="#fff" stroke-width="1.6"/><path d="M9 4a3 3 0 0 1 3 3c0 2-3 6-3 6s-3-4-3-6a3 3 0 0 1 3-3z" fill="#fff"/></svg>12, MERCHANT LANE</div>
    <div class="office-line"><svg width="18" height="18" viewBox="0 0 18 18"><circle cx="9" cy="9" r="8" fill="none" stroke="#fff" stroke-width="1.6"/><path d="M6 5l2 0 1 2-1 1a5 5 0 0 0 2 2l1-1 2 1v2c-4 0-7-3-7-7z" fill="#fff"/></svg>(356) 2100 0001</div>
    <h4 style="margin-top:18px">BIRKIRKARA</h4>
    <div class="office-line"><svg width="18" height="18" viewBox="0 0 18 18"><circle cx="9" cy="9" r="8" fill="none" stroke="#fff" stroke-width="1.6"/><path d="M9 4a3 3 0 0 1 3 3c0 2-3 6-3 6s-3-4-3-6a3 3 0 0 1 3-3z" fill="#fff"/></svg>88, ORCHARD ROAD</div>
    <div class="office-line"><svg width="18" height="18" viewBox="0 0 18 18"><circle cx="9" cy="9" r="8" fill="none" stroke="#fff" stroke-width="1.6"/><path d="M6 5l2 0 1 2-1 1a5 5 0 0 0 2 2l1-1 2 1v2c-4 0-7-3-7-7z" fill="#fff"/></svg>(356) 2100 0002</div>
    <div class="office-line" style="margin-top:28px"><svg width="18" height="18" viewBox="0 0 18 18"><circle cx="9" cy="9" r="8" fill="none" stroke="#fff" stroke-width="1.6"/><rect x="5" y="6" width="8" height="6" fill="none" stroke="#fff" stroke-width="1.2"/></svg>info@mallia-sant.example</div>
  </div>

  <div class="footer-brand">Mallia &amp; Sant Advocates</div>
  <div class="social"><span></span><span></span><span></span></div>
</footer>

<div class="copyright">COPYRIGHT © 2016 MALLIA &amp; SANT ADVOCATES. ALL RIGHTS RESERVED.</div>

</body>
</html>
```